Psychiatric Office Needs a Website- 1st Time Ever!

Been in practice since 2003 with no website, but finally ready to dive in. We are Maplecrest Behavioral Healthcare, a mental health outpatient practice based in Fayetteville, Georgia that sees diverse individuals and families from childhood to advanced age for a variety of conditions. We've grown by word of mouth and referral but would now like to have a digital footprint. Be the pioneer of our website and we will be sure to share. We would like to see designs that are modern, animated, fairly colorful, easy to read, and caters to all ages. Also, we would like the design to take the whole page (not be centered) and can be viewed well on phone/tablet. Please see our outline for more information. Our motto/slogan is: Maplecrest Behavioral Healthcare- A step forward in your wellness journey, so the design should try to reflect that.
Updates

Project Deadline Extended
Reason: site in progress

Target Market(s)

Children through elderly

Industry/Entity Type

Medical

Logo Text

Stepping forward in your wellness journey

Number of Pages Required

1 page

Colors

Designer to choose colors to be used in the design.

Requirements
Must have
• Animation or moving pictures.
• Color.
• Concise.
• User friendly
• Diversity in the stock photos

```html
<!DOCTYPE html>
<html lang="en">
<head>
<meta charset="utf-8">
<title>Maplecrest Behavioral Healthcare</title>
<link href="https://fonts.googleapis.com/css2?family=Lato:wght@300;400;700;900&display=swap" rel="stylesheet">
<style>
:root{
  --yellow:#f6b900;
  --yellow-light:#ffd23f;
  --yellow-deep:#eaa400;
  --ink:#2a2a2a;
  --dark:#262626;
  --darker:#1b1b1b;
  --grey:#6a6a6a;
  --white:#ffffff;
  --line:#e6e6e6;
}
*{margin:0;padding:0;box-sizing:border-box}
html,body{width:1200px;height:3452px;overflow:hidden}
body{font-family:"Lato",Arial,sans-serif;color:var(--ink);background:var(--white);position:relative}
.abs{position:absolute}
p{line-height:1.5}

/* Hero */
.hero{left:0;top:0;width:1200px;height:720px;overflow:hidden}
.hero-photo{left:0;top:0;width:1200px;height:720px;background:linear-gradient(180deg,#7d8a6a 0%,#a5ad8d 35%,#c9c2ae 60%,#8a7a66 100%)}
.topbar{left:0;top:0;width:1200px;height:34px;background:rgba(0,0,0,.55);color:#fff;font-size:13px}
.topbar span{position:absolute;top:9px}
.nav{left:0;top:34px;width:1200px;height:86px;background:rgba(255,255,255,.9)}
.brand{left:60px;top:12px;display:flex;align-items:center;gap:12px}
.brand-dot{width:58px;height:58px;border-radius:50%;background:var(--yellow)}
.brand-name{font-size:17px;font-weight:700;color:var(--ink);width:150px;line-height:1.2}
.menu{left:356px;top:0;display:flex;height:86px;align-items:center}
.menu a{font-size:15px;color:var(--ink);text-decoration:none;padding:0 16px}
.menu a.active{background:var(--yellow);color:#fff;height:120px;margin-top:-34px;display:flex;align-items:center;padding:0 30px}
.hero-title{left:0;top:290px;width:1200px;text-align:center;color:#fff}
.hero-title h1{font-size:44px;font-weight:400;letter-spacing:.5px}
.hero-title p{font-size:18px;margin-top:6px}
.btn{display:inline-block;background:var(--yellow);color:#fff;font-size:15px;font-weight:700;padding:12px 26px;border-radius:3px;letter-spacing:.5px}
.hero-btn{left:528px;top:396px}

/* Vision & Mission */
.vm{left:0;top:720px;width:1200px;height:340px}
.vm-left{left:0;top:0;width:600px;height:340px;background:var(--yellow)}
.vm-right{left:600px;top:0;width:600px;height:340px;background:var(--white)}
.vm h2{font-size:30px;font-weight:400;letter-spacing:1px;display:flex;align-items:center;gap:12px}
.vm p{font-size:14px;margin-top:16px}
.vision{left:70px;top:60px;width:380px;color:#fff}
.mission{left:770px;top:60px;width:380px;color:var(--ink)}
.mission h2{color:var(--yellow)}
.seal{left:460px;top:30px;width:280px;height:280px;border-radius:50%;background:var(--yellow);border:10px solid #fff;box-shadow:0 0 0 3px var(--yellow);display:flex;align-items:center;justify-content:center;text-align:center;color:#fff;font-size:20px;font-weight:700;padding:30px}

/* Services */
.services{left:0;top:1060px;width:1200px;height:880px;background:linear-gradient(180deg,#3b3b3b,#222 60%,#2d2d2d)}
.sec-title{left:0;width:1200px;text-align:center;font-size:32px;font-weight:400;letter-spacing:2px}
.services .sec-title{top:50px;color:#fff}
.services .sec-title::after{content:"";display:block;width:60px;height:3px;background:var(--yellow);margin:10px auto 0}
.svc-art{left:0;top:0}
.svc{width:240px;color:#fff;font-size:13px}
.svc h3{font-size:17px;font-weight:400;color:var(--yellow);margin-bottom:4px}
.svc b{font-weight:700;text-decoration:underline}

/* Conditions */
.conditions{left:0;top:1940px;width:1200px;height:500px;background:linear-gradient(180deg,var(--yellow-light),var(--yellow))}
.conditions .sec-title{top:48px;color:#fff;font-weight:700}
.cards{left:100px;top:130px;display:flex;gap:24px}
.card{width:232px;text-align:center}
.card .ph{width:232px;height:180px}
.card h3{font-size:18px;font-weight:700;margin-top:14px;color:var(--ink)}
.card p{font-size:12px;margin-top:10px;color:#5a4400}
.arrow{top:245px;width:30px;height:48px;background:#fff;display:flex;align-items:center;justify-content:center}

/* FAQ & News */
.faq{left:60px;top:2480px;width:520px}
.news{left:640px;top:2480px;width:500px}
.col-title{font-size:30px;color:var(--yellow);font-weight:400;letter-spacing:1px;padding-bottom:10px;border-bottom:1px solid var(--line)}
.faq-item{font-size:15px;color:var(--yellow-deep);padding:9px 0;display:flex;gap:10px;align-items:center}
.faq-open{background:#fafafa;border:1px solid var(--line);padding:10px 14px;margin-top:12px}
.faq-body{font-size:12px;color:var(--grey);padding:8px 14px}
.plus{width:16px;height:16px;border-radius:50%;background:var(--yellow);color:#fff;font-size:12px;display:flex;align-items:center;justify-content:center;font-weight:700}
.news-item{display:flex;gap:18px;padding:18px 0;border-bottom:1px solid var(--line)}
.news-item .ph{width:100px;height:80px;flex:none;border-radius:50%}
.news-item h4{font-size:14px;font-weight:400;color:var(--yellow-deep)}
.news-item p{font-size:12px;color:var(--grey);margin-top:4px}
.news-item small{display:block;font-size:11px;color:var(--yellow-deep);margin-top:6px}

/* CTA */
.cta{left:0;top:2870px;width:1200px;height:100px;background:var(--yellow)}
.cta p{position:absolute;left:60px;top:28px;width:760px;color:#fff;font-size:14px}
.cta .btn{position:absolute;left:900px;top:26px;background:#fff;color:var(--ink);border:2px solid #fff}

/* Footer */
.footer{left:0;top:2970px;width:1200px;height:440px;background:linear-gradient(180deg,#2e2e2e,var(--darker))}
.footer h4{font-size:16px;font-weight:400;letter-spacing:1px;color:#fff;margin-bottom:18px}
.f-col{top:40px;color:#ddd;font-size:13px}
.field{width:300px;height:34px;background:#fff;border-radius:2px;margin-bottom:12px;color:#999;font-size:12px;padding:9px 10px}
.field.tall{height:90px}
.f-btn{width:140px;height:36px;background:var(--yellow);color:#fff;font-weight:700;font-size:14px;display:flex;align-items:center;justify-content:center}
.f-list li{list-style:none;padding:5px 0;display:flex;gap:8px;align-items:center}
.f-list li::before{content:"";width:6px;height:6px;background:var(--yellow);border-radius:50%}
.find li{list-style:none;display:flex;gap:12px;align-items:flex-start;margin-bottom:14px;line-height:1.4}
.find .ic{width:22px;height:22px;border-radius:50%;background:var(--yellow);flex:none}
.socials{display:flex;gap:12px;margin-top:10px}
.socials span{width:34px;height:34px;border-radius:50%;background:var(--yellow);display:block}
.copyright{left:0;top:3410px;width:1200px;height:42px;background:#141414;color:#bbb;font-size:12px;text-align:center;padding-top:14px;letter-spacing:.5px}
</style>
</head>
<body>

<!-- Hero -->
<section class="abs hero">
  <div class="abs hero-photo" role="img" aria-label="Photo of a person relaxing on a park bench among green trees"></div>
  <div class="abs topbar">
    <span style="left:460px">Monday - Friday : 10:00 AM to 8:00 PM</span>
    <span style="left:740px">+1 555-014-2290</span>
    <span style="left:900px">LOGIN</span>
    <span style="left:1030px">Patient</span>
  </div>
  <nav class="abs nav">
    <div class="abs brand"><span class="brand-dot"></span><span class="brand-name">Maplecrest Behavioral Healthcare</span></div>
    <div class="abs menu">
      <a class="active">Home</a><a>About Us</a><a>Services</a><a>Conditions We Treat</a><a>New Patients</a><a>Contact Us</a>
    </div>
  </nav>
  <div class="abs hero-title">
    <h1>Maplecrest Behavioral Healthcare</h1>
    <p>A step forward in your wellness journey</p>
  </div>
  <span class="abs btn hero-btn">CONTACT US</span>
</section>

<!-- Vision & Mission -->
<section class="abs vm">
  <div class="abs vm-left"></div>
  <div class="abs vm-right"></div>
  <div class="abs vision">
    <h2><svg width="30" height="30" viewBox="0 0 30 30"><circle cx="15" cy="15" r="13" fill="none" stroke="#fff" stroke-width="2"/><circle cx="15" cy="15" r="5" fill="#fff"/></svg>VISION</h2>
    <p>We picture a community where every child, adult and elder can find calm, caring support close to home. Our team works to make mental health care simple to reach, warm to receive and built around each family we serve, now and for many years ahead.</p>
  </div>
  <div class="abs seal">Maplecrest Behavioral Healthcare</div>
  <div class="abs mission">
    <h2><svg width="30" height="30" viewBox="0 0 30 30"><path d="M6 26V4l18 7-18 7" fill="none" stroke="#f6b900" stroke-width="2.5"/></svg>MISSION</h2>
    <p>Our mission is to offer thoughtful outpatient care for people of every age and background. We listen first, plan together and walk beside each patient with respect, so every visit becomes one more step forward in a steady and hopeful wellness journey.</p>
  </div>
</section>

<!-- Services -->
<section class="abs services">
  <h2 class="abs sec-title">SERVICES</h2>
  <svg class="abs svc-art" width="1200" height="880" viewBox="0 0 1200 880">
    <g stroke="#f6b900" stroke-width="3">
      <line x1="600" y1="400" x2="470" y2="220"/><line x1="600" y1="400" x2="730" y2="220"/>
      <line x1="600" y1="400" x2="410" y2="380"/><line x1="600" y1="400" x2="790" y2="380"/>
      <line x1="600" y1="400" x2="450" y2="550"/><line x1="600" y1="400" x2="750" y2="550"/>
      <line x1="600" y1="400" x2="600" y2="620"/>
    </g>
    <circle cx="600" cy="400" r="105" fill="#fff"/>
    <circle cx="600" cy="400" r="95" fill="#f6b900"/>
    <text x="600" y="394" text-anchor="middle" fill="#fff" font-family="Lato,Arial,sans-serif" font-size="17" font-weight="700">Maplecrest</text>
    <text x="600" y="416" text-anchor="middle" fill="#fff" font-family="Lato,Arial,sans-serif" font-size="17" font-weight="700">Behavioral</text>
    <g fill="#f6b900">
      <circle cx="470" cy="220" r="58"/><circle cx="730" cy="220" r="58"/>
      <circle cx="410" cy="380" r="58"/><circle cx="790" cy="380" r="58"/>
      <circle cx="450" cy="550" r="58"/><circle cx="750" cy="550" r="58"/>
      <circle cx="600" cy="620" r="58"/>
    </g>
    <g fill="#b9a88e">
      <circle cx="470" cy="220" r="52" role="img" aria-label="Photo of a clinician meeting a patient"/>
      <circle cx="730" cy="220" r="52" role="img" aria-label="Photo of a work assessment meeting"/>
      <circle cx="410" cy="380" r="52" role="img" aria-label="Photo of medication consultation"/>
      <circle cx="790" cy="380" r="52" role="img" aria-label="Photo of a child during assessment"/>
      <circle cx="450" cy="550" r="52" role="img" aria-label="Photo of a pre-surgical consultation"/>
      <circle cx="750" cy="550" r="52" role="img" aria-label="Photo of a counselling session"/>
      <circle cx="600" cy="620" r="52" role="img" aria-label="Photo of a parent and child"/>
    </g>
  </svg>
  <div class="abs svc" style="left:150px;top:175px"><h3>Diagnostic evaluation and treatment</h3>Careful review of each concern with a clear care plan. <b>READ MORE</b></div>
  <div class="abs svc" style="left:810px;top:175px"><h3>Disability and work related reports</h3>Detailed reports that support work and benefit needs. <b>READ MORE</b></div>
  <div class="abs svc" style="left:110px;top:340px"><h3>Psychopharmacology</h3>Safe medication planning with steady follow up care. <b>READ MORE</b></div>
  <div class="abs svc" style="left:870px;top:340px"><h3>Early Childhood Assessments</h3>Gentle screening that helps young children thrive. <b>READ MORE</b></div>
  <div class="abs svc" style="left:140px;top:520px"><h3>Bariatric pre-surgical consultation</h3>Readiness reviews that prepare patients for surgery. <b>READ MORE</b></div>
  <div class="abs svc" style="left:830px;top:520px"><h3>Substance abuse assessments</h3>Honest, private reviews that open a path to recovery. <b>READ MORE</b></div>
  <div class="abs svc" style="left:480px;top:700px;text-align:center"><h3>Developmental disabilities</h3>Support plans shaped around each person and family. <b>READ MORE</b></div>
</section>

<!-- Conditions -->
<section class="abs conditions">
  <h2 class="abs sec-title">CONDITIONS WE TREAT</h2>
  <div class="abs arrow" style="left:30px"><svg width="12" height="18"><path d="M10 2L3 9l7 7" fill="none" stroke="#f6b900" stroke-width="3"/></svg></div>
  <div class="abs arrow" style="left:1140px"><svg width="12" height="18"><path d="M2 2l7 7-7 7" fill="none" stroke="#f6b900" stroke-width="3"/></svg></div>
  <div class="abs cards">
    <div class="card"><div class="ph" role="img" aria-label="Photo of a person feeling low" style="background:linear-gradient(135deg,#6e6a64,#a89c8c)"></div><h3>Mood Disorders</h3><p>Care for depression, bipolar and other changes in mood that shape daily life.</p></div>
    <div class="card"><div class="ph" role="img" aria-label="Photo of a counsellor with a worried patient" style="background:linear-gradient(135deg,#8da0b3,#c9c0b0)"></div><h3>Anxiety Disorders</h3><p>Help for worry, panic and stress so calm returns to home, school and work.</p></div>
    <div class="card"><div class="ph" role="img" aria-label="Photo of a group therapy session" style="background:linear-gradient(135deg,#9a8a78,#d0c2a8)"></div><h3>Psychotic Disorders</h3><p>Steady treatment and family support for clearer thinking and daily balance.</p></div>
    <div class="card"><div class="ph" role="img" aria-label="Photo of a mother and young child" style="background:linear-gradient(135deg,#7a5a48,#c79a78)"></div><h3>Common Disorders<br>of Childhood</h3><p>Attention, behavior and learning support for kids and the adults who love them.</p></div>
  </div>
</section>

<!-- FAQ -->
<section class="abs faq">
  <h2 class="col-title">FAQ</h2>
  <div class="faq-open">
    <div class="faq-item" style="padding:0"><span class="plus">−</span>What do I need to bring with me to my first visit?</div>
  </div>
  <p class="faq-body">Please bring a photo ID, your insurance card, a list of current medications and any past records. Arrive fifteen minutes early to finish your new patient forms.</p>
  <div class="faq-item"><span class="plus">+</span>How long do I have to wait to be seen?</div>
  <div class="faq-item"><span class="plus">+</span>Who is my child not doing well in school?</div>
  <div class="faq-item"><span class="plus">+</span>What type of insurance do you accept?</div>
</section>

<!-- News -->
<section class="abs news">
  <h2 class="col-title">LATEST NEWS</h2>
  <div class="news-item"><div class="ph" role="img" aria-label="Photo of a smiling family outdoors" style="background:linear-gradient(135deg,#a3b08a,#d8c9a4)"></div><div><h4>New evening hours for working families</h4><p>Appointments now open later on weekdays for your comfort.</p><small>READ MORE</small></div></div>
  <div class="news-item"><div class="ph" role="img" aria-label="Photo of a clinician writing notes" style="background:linear-gradient(135deg,#9c8f82,#d6cab9)"></div><div><h4>Tips for a calm start to the school year</h4><p>Simple routines that help children settle in with ease.</p><small>READ MORE</small></div></div>
</section>

<!-- CTA -->
<section class="abs cta">
  <p>New to our practice? Complete the patient form before your first visit so our team can prepare for you. It only takes a few minutes and helps us plan the care that fits your needs best.</p>
  <span class="btn">NEW PATIENT FORM</span>
</section>

<!-- Footer -->
<footer class="abs footer">
  <div class="abs f-col" style="left:60px">
    <h4>QUICK INQUIRY</h4>
    <div class="field">Name*</div>
    <div class="field">Email*</div>
    <div class="field">Services*</div>
    <div class="field tall">Message*</div>
    <div class="f-btn">SUBMIT</div>
  </div>
  <div class="abs f-col" style="left:500px">
    <h4>OUR SERVICES</h4>
    <ul class="f-list"><li>Home</li><li>About Us</li><li>Services</li><li>Conditions We Treat</li><li>New Patients</li><li>Contact Us</li></ul>
  </div>
  <div class="abs f-col" style="left:860px;width:280px">
    <h4>FIND US</h4>
    <ul class="find">
      <li><span class="ic"></span>Maplecrest Behavioral Healthcare<br>214 Willow Bend Road, Fayetteville GA</li>
      <li><span class="ic"></span>+1 555-014-2290</li>
      <li><span class="ic"></span>+1 555-014-2291</li>
      <li><span class="ic"></span>hello@maplecrestbh.example</li>
    </ul>
    <div class="socials"><span></span><span></span><span></span></div>
  </div>
</footer>
<div class="abs copyright">© MAPLECREST BEHAVIORAL HEALTHCARE · 2017 All Rights Reserved</div>

</body>
</html>
```